A new presentation to our clients

we are a Real Estate agency, our website is www.lumibrasa.com and it’s time to have a new, fashion and remarcable Business Card. we want to differentiate ourselves from other companies so we want a business card that differentiates us. we want the business card to impact our customers. in the competitive market that we have today, we have to be different and it is this difference that we seek

Target Market(s)

Real Estate Clients

Contact Information for Business Card

We search a totaly diferent card from the usual

Font styles to use
Sans Serif

Colors
e34197

Requirements
Must have
• Logo, adress, phone contact, e-mail, photo, and our website
Nice to have
• We would like to see a modern business card
Should not have
• Houses or building draws

```html
<!DOCTYPE html>
<html lang="pt">
<head>
<meta charset="utf-8">
<title>Lumi Brasa – Business Card</title>
<link rel="stylesheet" href="https://fonts.googleapis.com/css2?family=Montserrat:wght@600;700&family=Questrial&display=swap">
<style>
  :root {
    --backdrop: #2b2b2b;
    --card: #ffffff;
    --brand-pink: #e8246c;
    --name-ink: #454545;
    --body-ink: #6a6a6a;
    --logo-ink: #ffffff;
  }
  * { margin: 0; padding: 0; box-sizing: border-box; }
  html, body {
    width: 1200px; height: 791px; overflow: hidden;
    background: var(--backdrop);
  }
  .business-card {
    position: absolute; left: 50px; top: 82px;
    width: 1100px; height: 627px;
    background: var(--card);
    border-radius: 36px;
    overflow: hidden;
  }
  .brand-panel {
    position: absolute; inset: 0; width: 100%; height: 100%;
  }
  .brand-panel path { fill: var(--brand-pink); }
  .brand-name {
    position: absolute; left: 539px; width: 561px; top: 270px;
    text-align: center;
    font: 600 66px/1 "Montserrat", sans-serif;
    color: var(--logo-ink);
    letter-spacing: 1px;
    white-space: nowrap;
  }
  .contact-row {
    position: absolute; left: 122px;
    font: 400 23px/1 "Questrial", sans-serif;
    color: var(--body-ink);
    white-space: nowrap;
  }
  .contact-icon {
    position: absolute; left: 74px; width: 24px; height: 24px;
    fill: var(--brand-pink);
  }
  .person-name {
    position: absolute; left: 122px; top: 170px;
    font: 700 36px/1 "Montserrat", sans-serif;
    color: var(--name-ink);
    white-space: nowrap;
  }
  .person-role {
    position: absolute; left: 122px; top: 213px;
    font: 600 23px/1 "Montserrat", sans-serif;
    color: var(--name-ink);
    white-space: nowrap;
  }
</style>
</head>
<body>
  <main class="business-card">
    <svg class="brand-panel" viewBox="0 0 800 456" preserveAspectRatio="none" aria-hidden="true">
      <path d="M606 0 C480 0 391 105 391 228 C391 355 490 456 600 456 L800 456 L800 0 Z"/>
    </svg>
    <div class="brand-name">Lumi Brasa</div>

    <svg class="contact-icon" style="top:176px" viewBox="0 0 24 24" aria-hidden="true">
      <circle cx="12" cy="7" r="5"/><path d="M2 23 C2 16 6 13 12 13 C18 13 22 16 22 23 Z"/>
    </svg>
    <h1 class="person-name">NUNO FALCATO</h1>
    <p class="person-role">CEO/FOUNDER</p>

    <svg class="contact-icon" style="top:258px;height:30px" viewBox="0 0 24 30" aria-hidden="true">
      <path d="M12 1 C5.9 1 2 5.5 2 11 C2 18 12 29 12 29 C12 29 22 18 22 11 C22 5.5 18.1 1 12 1 Z M12 7 A4 4 0 1 1 12 15 A4 4 0 1 1 12 7 Z" fill-rule="evenodd"/>
    </svg>
    <p class="contact-row" style="top:258px">Av. das Camélias, 418</p>
    <p class="contact-row" style="top:288px">4710-251, Braga</p>

    <svg class="contact-icon" style="top:336px" viewBox="0 0 24 24" aria-hidden="true">
      <path d="M5 2 L9 2 L11 7 L8.5 9 C9.8 12 12 14.2 15 15.5 L17 13 L22 15 L22 19 C22 21 20.5 22 19 22 C10 21.5 2.5 14 2 5 C2 3.5 3 2 5 2 Z"/>
    </svg>
    <p class="contact-row" style="top:336px">(+351) 225 410 386</p>

    <svg class="contact-icon" style="top:368px" viewBox="0 0 24 24" aria-hidden="true">
      <path d="M6 2 H16 L18 4 V9 H6 Z M2 10 H22 V19 H18 V16 H6 V19 H2 Z M7 17 H17 V22 H7 Z"/>
    </svg>
    <p class="contact-row" style="top:368px">(+351) 225 410 387</p>

    <svg class="contact-icon" style="top:400px" viewBox="0 0 24 24" aria-hidden="true">
      <path d="M2 5 H22 V19 H2 Z"/>
      <path d="M3 6 L12 13 L21 6" stroke="#fff" stroke-width="1.6" fill="none"/>
    </svg>
    <p class="contact-row" style="top:400px">geral@lumibrasa.com</p>

    <svg class="contact-icon" style="top:432px" viewBox="0 0 24 24" aria-hidden="true">
      <circle cx="12" cy="12" r="10"/>
      <path d="M2 12 H22 M12 2 C8 6 8 18 12 22 M12 2 C16 6 16 18 12 22" stroke="#fff" stroke-width="1.4" fill="none"/>
    </svg>
    <p class="contact-row" style="top:432px">www.lumibrasa.com</p>
  </main>
</body>
</html>
```